Pipe Repair Clamps

A double side A4 showing our pipe repair clamps for stopping leaking pipes within seconds. For water , sewage companies, hotels, malls, airports, hosptals, facilities management companies and district cooling companies. Reverse side will show a size chart. Examples of product uploaded

```html
<!DOCTYPE html>
<html lang="en">
<head>
<meta charset="utf-8">
<title>Harbourline Couplings – Repair Clamp Size Chart</title>
<link href="https://fonts.googleapis.com/css2?family=IBM+Plex+Mono:wght@400;500&family=Open+Sans:wght@400;600;700&display=swap" rel="stylesheet">
<style>
:root{
  --head:#c0562b;
  --row-alt:#e6f0df;
  --rule:#5aa05a;
  --blue:#1f8ed0;
  --blue-soft:#5b8fcc;
  --spec-head:#4f87c2;
  --spec-row:#e3e5e8;
  --spec-alt:#d6d9dd;
  --ink:#222;
  --white:#ffffff;
}
*{margin:0;padding:0;box-sizing:border-box}
html,body{width:927px;height:1200px;overflow:hidden}
body{position:relative;font-family:"Open Sans",sans-serif;color:var(--ink);
  background:linear-gradient(180deg,#eceef0 0%,#e9e8e9 55%,#ebd9d4 78%,#e3d6cc 100%)}
.abs{position:absolute}
.size-chart{left:64px;top:36px;width:533px;border-collapse:collapse;font-family:"IBM Plex Mono",monospace;font-size:7.6px;text-align:center}
.size-chart th{background:var(--head);color:#fff;font-weight:400;height:28px;line-height:11px;font-size:6.8px}
.size-chart td{height:17.35px}
.size-chart tbody tr:nth-child(even){background:var(--row-alt)}
.size-chart tbody tr:nth-child(odd){background:rgba(255,255,255,.55)}
.size-chart tbody tr:last-child td{border-bottom:2px solid var(--rule)}
.note{left:70px;top:682px;font-size:7.4px;color:#333}
.hero-photo{left:624px;top:0;width:268px;height:628px;
  background:linear-gradient(160deg,#8b8d90 0%,#5f6266 30%,#3c6f86 48%,#9fb9c4 62%,#5a5b5d 80%,#7c7e80 100%)}
.brand{left:676px;top:112px;display:flex;align-items:center;gap:8px;color:var(--white);font-weight:700;font-size:17px;letter-spacing:.5px}
.brand .dot{width:14px;height:14px;border-radius:50%;background:var(--white);flex:none}
.section-title{font-weight:700;color:var(--blue);font-size:22px;line-height:27px;text-align:right}
.hdpe{left:80px;top:722px;width:104px}
.arrow{left:196px;top:724px}
.product{border-radius:6px}
.hdpe-photo{left:92px;top:824px;width:108px;height:108px;background:linear-gradient(135deg,#6b6d70,#3b3c3e)}
.spec{left:251px;top:718px;width:349px}
.spec-head{background:var(--spec-head);color:#fff;text-align:center;font-weight:700;font-size:14px;height:25px;line-height:25px}
.spec-row{display:flex;height:21.9px;line-height:21.9px;font-size:13px;background:var(--spec-row)}
.spec-row:nth-child(odd){background:var(--spec-alt)}
.spec-row span{flex:1;padding-left:38px}
.spec-row span+span{text-align:right;padding-right:8px;border-left:1px solid #f2f2f2}
.tool-title{color:var(--blue-soft);font-weight:600;font-size:23px;line-height:29px;text-align:center;width:230px}
.leak{left:642px;top:674px}
.leak-photo{left:632px;top:738px;width:252px;height:54px;background:linear-gradient(170deg,transparent 30%,#9a9ca0 48%,transparent 56%)}
.tape{left:642px;top:813px}
.tape-photo{left:656px;top:848px;width:228px;height:82px;background:radial-gradient(ellipse at 70% 50%,#fbfbf9 40%,#d8d7d2 70%,transparent 72%)}
.skyline{left:0;top:905px;width:927px;height:220px;
  background:linear-gradient(180deg,rgba(150,160,170,0) 0%,rgba(150,160,170,.5) 40%,#8b8f93 70%,#b89f8e 85%,rgba(226,214,204,0) 100%)}
.site{left:0;width:927px;text-align:center;top:1131px;font-weight:700;font-size:21px;color:#222}
.group{left:0;width:927px;text-align:center;top:1160px;font-weight:600;font-size:12.5px;letter-spacing:.4px}
</style>
</head>
<body>
<table class="size-chart abs">
<colgroup><col style="width:40px"><col style="width:84px"><col style="width:40px"><col style="width:40px"><col style="width:36px"><col style="width:24px"><col style="width:34px"><col style="width:86px"><col style="width:68px"><col style="width:38px"><col style="width:43px"></colgroup>
<thead><tr><th>OD<br>(mm)</th><th>ODmin-ODmax<br>(mm)</th><th>PN<br>(mm)</th><th>WP<br>(bar)</th><th>C<br>(mm)</th><th>l1<br>(mm)</th><th>l2<br>(mm)</th><th>D<br>(mm)</th><th>H<br>(mm)</th><th>M</th><th>Nm</th></tr></thead>
<tbody>
<tr><td>21.7</td><td>21-23</td><td>16</td><td>32</td><td>3</td><td>57</td><td>–</td><td>35</td><td>50</td><td>6</td><td>15</td></tr>
<tr><td>25</td><td>24.5-25.5</td><td>16</td><td>32</td><td>3</td><td>57</td><td>–</td><td>50</td><td>70</td><td>6</td><td>15</td></tr>
<tr><td>27.2</td><td>26-28</td><td>16</td><td>32</td><td>3</td><td>57</td><td>–</td><td>50</td><td>70</td><td>6</td><td>15</td></tr>
<tr><td>32</td><td>31.5-32.5</td><td>16</td><td>32</td><td>3</td><td>57</td><td>–</td><td>55</td><td>75</td><td>6</td><td>15</td></tr>
<tr><td>34</td><td>33-35</td><td>16</td><td>32</td><td>3</td><td>57</td><td>–</td><td>55</td><td>75</td><td>6</td><td>15</td></tr>
<tr><td>40</td><td>39.5-41.5</td><td>16</td><td>32</td><td>5</td><td>57</td><td>–</td><td>55</td><td>75</td><td>6</td><td>15</td></tr>
<tr><td>42</td><td>42-44</td><td>16</td><td>32</td><td>5</td><td>57</td><td>–</td><td>65</td><td>85</td><td>6</td><td>15</td></tr>
<tr><td>44.5</td><td>44-45.1</td><td>16</td><td>32</td><td>5</td><td>57</td><td>–</td><td>65</td><td>85</td><td>6</td><td>15</td></tr>
<tr><td>48.6</td><td>47-49</td><td>16</td><td>32</td><td>5</td><td>57</td><td>100</td><td>70</td><td>90</td><td>6</td><td>15</td></tr>
<tr><td>54</td><td>53.3-54.6</td><td>16</td><td>32</td><td>5</td><td>57</td><td>100</td><td>70</td><td>90</td><td>8</td><td>30</td></tr>
<tr><td>57</td><td>56.3-57.7</td><td>16</td><td>32</td><td>5</td><td>57</td><td>100</td><td>50</td><td>100</td><td>8</td><td>30</td></tr>
<tr><td>60.3</td><td>59-62</td><td>16</td><td>32</td><td>5</td><td>80</td><td>139</td><td>85</td><td>105</td><td>8</td><td>30</td></tr>
<tr><td>63</td><td>62.2-63.9</td><td>16</td><td>32</td><td>5</td><td>80</td><td>139</td><td>85</td><td>105</td><td>8</td><td>30</td></tr>
<tr><td>76.1</td><td>75-78</td><td>14</td><td>28</td><td>5</td><td>80</td><td>139</td><td>100</td><td>120</td><td>8</td><td>30</td></tr>
<tr><td>79.9</td><td>78.8-80.8</td><td>14</td><td>28</td><td>5</td><td>80</td><td>139</td><td>100</td><td>120</td><td>8</td><td>30</td></tr>
<tr><td>88.9</td><td>88-92</td><td>14</td><td>28</td><td>5</td><td>107</td><td>203</td><td>110</td><td>130</td><td>10</td><td>50</td></tr>
<tr><td>108</td><td>106-110</td><td>14</td><td>28</td><td>5</td><td>107</td><td>203</td><td>130</td><td>150</td><td>10</td><td>50</td></tr>
<tr><td>110</td><td>108.9-111.2</td><td>14</td><td>28</td><td>5</td><td>107</td><td>203</td><td>130</td><td>150</td><td>10</td><td>50</td></tr>
<tr><td>114.3</td><td>112-116</td><td>14</td><td>28</td><td>5</td><td>107</td><td>203</td><td>135</td><td>155</td><td>10</td><td>50</td></tr>
<tr><td>118</td><td>116.6-119.2</td><td>14</td><td>28</td><td>5</td><td>107</td><td>203</td><td>140</td><td>160</td><td>10</td><td>50</td></tr>
<tr><td>125</td><td>12.6-126.5</td><td>14</td><td>28</td><td>5</td><td>107</td><td>203</td><td>150</td><td>185</td><td>10</td><td>50</td></tr>
<tr><td>133</td><td>131.5-134.4</td><td>14</td><td>28</td><td>5</td><td>107</td><td>203</td><td>160</td><td>190</td><td>10</td><td>50</td></tr>
<tr><td>140</td><td>137-143</td><td>14</td><td>28</td><td>5</td><td>116</td><td>203</td><td>165</td><td>195</td><td>12</td><td>80</td></tr>
<tr><td>159</td><td>157-161</td><td>12</td><td>24</td><td>10</td><td>116</td><td>203</td><td>185</td><td>215</td><td>12</td><td>80</td></tr>
<tr><td>165.2</td><td>163.3-166.7</td><td>12</td><td>24</td><td>10</td><td>116</td><td>203</td><td>190</td><td>210</td><td>12</td><td>80</td></tr>
<tr><td>168</td><td>166-170</td><td>12</td><td>24</td><td>10</td><td>116</td><td>203</td><td>195</td><td>225</td><td>12</td><td>80</td></tr>
<tr><td>170</td><td>168.2-171.9</td><td>12</td><td>24</td><td>10</td><td>116</td><td>203</td><td>195</td><td>225</td><td>14</td><td>100</td></tr>
<tr><td>200</td><td>198.2-201.5</td><td>8</td><td>16</td><td>10</td><td>116</td><td>203</td><td>240</td><td>270</td><td>14</td><td>100</td></tr>
<tr><td>219</td><td>217-221</td><td>8</td><td>16</td><td>10</td><td>155</td><td>255</td><td>250</td><td>280</td><td>14</td><td>100</td></tr>
<tr><td>250</td><td>250-254</td><td>8</td><td>16</td><td>10</td><td>155</td><td>255</td><td>285</td><td>315</td><td>14</td><td>100</td></tr>
<tr><td>273</td><td>271-275</td><td>8</td><td>16</td><td>10</td><td>155</td><td>255</td><td>305</td><td>335</td><td>14</td><td>100</td></tr>
<tr><td>315</td><td>313-317</td><td>7</td><td>14</td><td>10</td><td>155</td><td>255</td><td>340</td><td>375</td><td>14</td><td>100</td></tr>
<tr><td>325</td><td>323-327</td><td>7</td><td>14</td><td>10</td><td>155</td><td>255</td><td>360</td><td>390</td><td>14</td><td>100</td></tr>
<tr><td>355.6</td><td>354-358</td><td>7</td><td>14</td><td>10</td><td>155</td><td>255</td><td>385</td><td>420</td><td>14</td><td>100</td></tr>
<tr><td>377</td><td>375-379</td><td>7</td><td>14</td><td>10</td><td>155</td><td>255</td><td>410</td><td>440</td><td>14</td><td>100</td></tr>
</tbody>
</table>
<p class="note abs">Some sizes and lengths not listed are avaliable upon request.</p>

<div class="hero-photo abs" role="img" aria-label="Blue repair clamp being fitted over a leaking pipe with water spraying out"></div>
<div class="brand abs"><span class="dot"></span>HARBOURLINE</div>

<h2 class="section-title hdpe abs">HDPE<br>REPAIR<br>SECTION</h2>
<svg class="arrow abs" width="36" height="26" viewBox="0 0 36 26"><path d="M2 13H30M20 3l11 10-11 10" fill="none" stroke="#1f8ed0" stroke-width="4"/></svg>
<div class="hdpe-photo product abs" role="img" aria-label="Dark grey HDPE split repair section with bolt flanges"></div>

<section class="spec abs">
<div class="spec-head">SPECIFICATION</div>
<div class="spec-list">
<div class="spec-row"><span>DN40MM</span><span>DN200MM</span></div>
<div class="spec-row"><span>DN50MM</span><span>DN225MM</span></div>
<div class="spec-row"><span>DN63MM</span><span>DN250MM</span></div>
<div class="spec-row"><span>DN75MM</span><span>DN280MM</span></div>
<div class="spec-row"><span>DN90MM</span><span>DN315MM</span></div>
<div class="spec-row"><span>DN110MM</span><span>DN355MM</span></div>
<div class="spec-row"><span>DN125MM</span><span>DN400MM</span></div>
<div class="spec-row"><span>DN140MM</span><span>DN450MM</span></div>
<div class="spec-row"><span>DN160MM</span><span>DN500MM</span></div>
<div class="spec-row"><span>DN180MM</span><span>DN630MM</span></div>
</div>
</section>

<h2 class="tool-title leak abs">LEAK<br>DETECTION TOOL</h2>
<div class="leak-photo abs" role="img" aria-label="Leak detection listening rod with round earpiece"></div>
<h2 class="tool-title tape abs">PIPE O.D. TAPE</h2>
<div class="tape-photo abs" role="img" aria-label="White pipe diameter measuring tape"></div>

<div class="skyline abs" role="img" aria-label="Hazy city skyline with towers and low-rise buildings"></div>
<p class="site abs">WWW.HARBOURLINECOUPLINGS.COM</p>
<p class="group abs">A MARDEN GROUP COMPANY</p>
</body>
</html>
```